Dynamic Business Card for Sports Supplements Company

Hi! I'm looking for an awesome business card to match my existing sports supplement company. I have uploaded my current company logo and screenshot of the front page of my website.

I would like to have something dynamic and interesting and utilize the colors in the website - the reds and purples

The business card should be double sided and focus on a unique eye-catching design on the back and include all the relevant company info.

Most importantly, it should say somewhere: "Sign up on our website for a coupon code."

Target Market(s)

Mostly for women gym goers but it shouldn't be too feminine. It should be in keeping with the website design. It should flow and clearly be connected to it

Industry/Entity Type

Business

Contact Information for Business Card

Lorraine K. Vestal
CEO
LVestal@Quorvanexco.com
www.quorvanexco.com
555.417.3820
P.O. Box 47315
Alder Falls, Ohio 00000

Sign up on our website for a coupon code

Font styles to use
Serif
Sans Serif
Other font styles liked:
• Novecento font family and "Quorvanex" is in AR Destine font

Requirements
Must have
• One side should be a bold Quorvanex logo design. Even just the symbol itself may be o.k. (see attached file)

```html
<!DOCTYPE html>
<html lang="en">
<head>
<meta charset="utf-8">
<title>Quorvanex Business Card</title>
<link rel="stylesheet" href="https://fonts.googleapis.com/css2?family=Open+Sans:wght@400;600;700;800&display=swap">
<style>
  :root {
    --brand-red: #e81e2c;
    --ink-black: #0c0c0c;
    --paper-white: #ffffff;
    --text-dark: #2b2b2b;
    --text-grey: #b4b4b4;
    --stage: #e9e6e2;
  }
  * { box-sizing: border-box; margin: 0; padding: 0; }
  html, body {
    width: 1200px; height: 950px; overflow: hidden;
    background: var(--stage);
    font-family: "Open Sans", Arial, sans-serif;
  }
  .stage {
    position: relative; width: 1200px; height: 950px;
    display: flex; justify-content: center; align-items: center; gap: 80px;
  }
  .card {
    position: relative; width: 400px; height: 700px;
    border-radius: 6px; overflow: hidden;
    box-shadow: 0 14px 30px rgba(0,0,0,0.25);
  }
  .card-front { background: var(--paper-white); }
  .front-shape { position: absolute; inset: 0; }
  .brand-lockup {
    position: absolute; top: 200px; left: 0; width: 100%;
    text-align: center;
  }
  .brand-name {
    font-weight: 800; font-size: 44px; letter-spacing: 1px; text-transform: uppercase;
    color: var(--paper-white); line-height: 1.1;
  }
  .brand-tagline {
    margin-top: 6px; font-size: 12px; letter-spacing: 3.6px; text-transform: uppercase;
    color: var(--text-grey); font-weight: 400;
  }
  .contact {
    position: absolute; top: 424px; left: 0; width: 100%;
    text-align: center; color: var(--text-dark);
  }
  .person-name {
    color: var(--brand-red); font-weight: 600; font-size: 25px;
    letter-spacing: 1.5px; text-transform: uppercase;
  }
  .person-role { font-size: 19px; margin-top: 2px; }
  .address { font-size: 19px; margin-top: 12px; line-height: 1.35; }
  .contact-lines {
    list-style: none; display: inline-block; text-align: left;
    margin-top: 6px; font-size: 19px; line-height: 1.45;
  }
  .contact-lines li { display: flex; align-items: center; gap: 7px; }
  .contact-lines svg { width: 15px; height: 15px; flex: none; }
  .card-back { background: var(--brand-red); }
  .back-badge {
    position: absolute; top: 200px; left: 30px; width: 340px; height: 250px;
    border-radius: 50%; background: var(--paper-white);
    display: flex; align-items: center; justify-content: center;
  }
  .back-badge-name {
    color: var(--brand-red); font-weight: 800; font-size: 40px;
    text-transform: uppercase; letter-spacing: 1px;
  }
  .coupon-line {
    position: absolute; bottom: 44px; left: 0; width: 100%;
    text-align: center; color: var(--paper-white); font-size: 18px;
  }
</style>
</head>
<body>
<main class="stage">
  <section class="card card-front" aria-label="Front of business card">
    <svg class="front-shape" viewBox="0 0 400 700" aria-hidden="true">
      <polygon points="0,0 400,0 400,300 200,385 0,300" fill="var(--ink-black)"/>
      <polygon points="0,300 200,385 400,300 400,314 200,399 0,314" fill="var(--brand-red)"/>
    </svg>
    <div class="brand-lockup">
      <div class="brand-name">Quorvanex</div>
      <div class="brand-tagline">Your Strength Companion</div>
    </div>
    <div class="contact">
      <div class="person-name">Lorraine K. Vestal</div>
      <div class="person-role">CEO</div>
      <div class="address">P.O. Box 47315<br>Alder Falls, Ohio 00000</div>
      <ul class="contact-lines">
        <li>
          <svg viewBox="0 0 16 16" aria-hidden="true"><path d="M4 1.5l2.2 3-1.4 1.6c.8 1.8 2.3 3.3 4.1 4.1l1.6-1.4 3 2.2-1 2.5C7.5 13.3 2.7 8.5 1.5 3.5z" fill="var(--brand-red)"/></svg>
          555.417.3820
        </li>
        <li>
          <svg viewBox="0 0 16 16" aria-hidden="true"><rect x="1" y="3" width="14" height="10" rx="1" fill="var(--brand-red)"/><path d="M1.5 4l6.5 5 6.5-5" stroke="#fff" stroke-width="1.2" fill="none"/></svg>
          LVestal@Quorvanexco.com
        </li>
        <li>
          <svg viewBox="0 0 16 16" aria-hidden="true"><circle cx="8" cy="8" r="7" fill="var(--brand-red)"/><path d="M1 8h14M8 1c-3 3.5-3 10.5 0 14M8 1c3 3.5 3 10.5 0 14" stroke="#fff" stroke-width="1" fill="none"/></svg>
          www.quorvanexco.com
        </li>
      </ul>
    </div>
  </section>

  <section class="card card-back" aria-label="Back of business card">
    <div class="back-badge">
      <span class="back-badge-name">Quorvanex</span>
    </div>
    <p class="coupon-line">Sign up on our website for a coupon code</p>
  </section>
</main>
</body>
</html>
```